I need a business card to give to prospective clients. I am a freelance photographer who photographs most things (except weddings and social stuff) including nature, wildlife and interiors.
I want to look modern and stylish.
I am including a photograph although I am by no means certain that it should be used - what do you think?
More of my images can be seen and downloaded at my PixVault page - just search for Maren Tolbeck
Target Market(s)
Home owners selling or letting properties, private individuals wanting to buy prints
Industry/Entity Type
Business
Contact Information for Business Card
Maren Tolbeck Photography
Maren
Wrenfield Cottage, Mossbank Road, Pelsworth, Carrow Heath, KX41 2RB
Tel: +44 7000 418263. Email: maren@tolbeckstudio.example

```html
<!DOCTYPE html>
<html lang="en">
<head>
<meta charset="utf-8">
<title>Maren Tolbeck Photography – Business Card</title>
<link rel="stylesheet" href="https://fonts.googleapis.com/css2?family=Lato:wght@400;700;900&display=swap">
<style>
  :root {
    --page-bg: #1d1d1d;
    --card-dark: #262626;
    --photo-top: #9a9a9a;
    --photo-mid: #6e6e6e;
    --photo-low: #303030;
    --white: #ffffff;
    --light-text: #d6d6d6;
    --muted-text: #bdbdbd;
    --accent-green: #1f9a3c;
  }
  * { margin: 0; padding: 0; box-sizing: border-box; }
  html, body {
    width: 1200px; height: 900px; overflow: hidden;
    background: var(--page-bg);
    font-family: "Lato", Arial, sans-serif;
  }
  .business-card {
    position: absolute; left: 100px; top: 147px;
    width: 1000px; height: 606px;
    background: var(--card-dark);
    overflow: hidden;
    box-shadow: 0 20px 50px rgba(0,0,0,0.6);
  }
  .card-photo {
    position: absolute; inset: 0;
    background: linear-gradient(180deg, var(--photo-top) 0%, var(--photo-mid) 40%, var(--photo-low) 72%, var(--card-dark) 100%);
  }
  .brand-name {
    position: absolute; left: 90px; top: 148px;
    font-weight: 900; font-size: 46px; letter-spacing: 0.5px;
    color: var(--white); text-transform: uppercase; line-height: 1;
  }
  .services {
    position: absolute; left: 250px; top: 300px;
    font-weight: 900; font-size: 36px; letter-spacing: 0.5px;
    color: var(--light-text); text-transform: uppercase;
  }
  .services .divider { color: var(--accent-green); font-weight: 400; padding: 0 6px; }
  .contact {
    position: absolute; left: 190px; top: 400px;
    color: var(--muted-text); font-size: 27px; font-weight: 400;
  }
  .contact-row { display: flex; align-items: center; gap: 18px; margin-bottom: 20px; }
  .contact-row .spacer { width: 60px; }
  .contact-icon { width: 28px; height: 28px; flex: none; fill: var(--muted-text); }
  .address-second { padding-left: 210px; margin-top: -10px; }
</style>
</head>
<body>
  <main class="business-card">
    <div class="card-photo" role="img" aria-label="Black and white close-up photograph of an elephant's legs lifting a foot in grass"></div>

    <h1 class="brand-name">Maren Tolbeck Photography</h1>

    <p class="services">Nature<span class="divider">|</span>Wildlife<span class="divider">|</span>Interiors</p>

    <div class="contact">
      <div class="contact-row">
        <svg class="contact-icon" viewBox="0 0 24 24" aria-hidden="true">
          <path d="M2 9c0-3 4-5 10-5s10 2 10 5v2h-5V9c-2-1-8-1-10 0v2H2zM5 12h14l2 8H3zM9 14a3 3 0 1 0 6 0 3 3 0 1 0-6 0z"/>
        </svg>
        <span>+44 7000 418263</span>
        <span class="spacer"></span>
        <svg class="contact-icon" viewBox="0 0 24 24" aria-hidden="true">
          <path d="M2 5h20v14H2z" fill="none" stroke="var(--muted-text)" stroke-width="2"/>
          <path d="M2 5l10 8 10-8" fill="none" stroke="var(--muted-text)" stroke-width="2"/>
        </svg>
        <span>maren@tolbeckstudio.example</span>
      </div>
      <div class="contact-row">
        <svg class="contact-icon" viewBox="0 0 24 24" aria-hidden="true">
          <path d="M12 2L1 12h3v10h6v-6h4v6h6V12h3z"/>
        </svg>
        <span>Wrenfield Cottage, Mossbank Road, Pelsworth,</span>
      </div>
      <div class="address-second">Carrow Heath, KX41 2RB</div>
    </div>
  </main>
</body>
</html>
```